Website for enterprise software start-up

We need a new Wordpress website. We are an early stage start-up focused on mobile video technology for cellular operators. The audience is strategy, marketing and customer acquisition execs from the operators.

The purpose of the site is to act as a sales brochure and capture leads. A demo app can be downloaded from the current site, want to put that behind a contact form.

Current website is at www.velmora.tv. Similar number of pages. Looking for a clean design template, with minimal customization. Blog will remain as is.

Want to be able to modify the copy via Wordpress. Reference designs I like: quandrix.com, briskfold7metrics.com

Target Market(s)

Mobile operators and MVNOs in the US and Asia Pacific regions

Industry/Entity Type

Business Software

Coding

Coded - Design and coding required

Number of Pages Required

4 page

Font styles to use
Sans Serif

Colors
f78f20

Requirements
Must have
• Form for downloading sample apps.
• Landing page with image, Product, Blog, About, Contact
• Team page

```html
<!DOCTYPE html>
<html lang="en">
<head>
<meta charset="utf-8">
<title>Velmora Media — High Quality Mobile Engagement</title>
<link rel="stylesheet" href="https://fonts.googleapis.com/css2?family=Questrial&family=Mulish:wght@700&family=Lato:wght@400;700&display=swap">
<style>
  :root {
    --brand-orange: #f78f20;
    --white: #ffffff;
    --footer-bg: #2b2b2b;
    --ink-dark: #2e2e2e;
    --hero-dark: #120f0e;
    --hero-mid: #4a4448;
    --hero-light: #a7a9b2;
    --badge-blue: #1d5fe0;
    --badge-silver: #e9edf0;
    --social-blue: #2f5ea8;
    --social-sky: #1da1e2;
    --social-red: #d9453a;
    --social-navy: #1b78b3;
  }
  * { margin: 0; padding: 0; box-sizing: border-box; }
  html, body { width: 1200px; height: 643px; overflow: hidden; }
  body { position: relative; font-family: "Questrial", sans-serif; color: var(--white); background: var(--hero-dark); }
  a { text-decoration: none; color: inherit; }

  .site-header {
    position: absolute; left: 0; top: 0; width: 1200px; height: 61px;
    background: var(--brand-orange);
  }
  .brand {
    position: absolute; left: 99px; top: 4px; width: 222px; height: 51px;
    background: var(--white);
    display: flex; align-items: center; gap: 10px; padding-left: 8px;
  }
  .brand-mark { width: 36px; height: 36px; background: var(--brand-orange); }
  .brand-name {
    font-family: "Mulish", sans-serif; font-weight: 700; font-size: 30px;
    color: var(--ink-dark); letter-spacing: -0.5px; line-height: 1;
  }
  .main-nav a {
    position: absolute; top: 18px; transform: translateX(-50%);
    font-size: 16px; color: var(--white); white-space: nowrap;
  }
  .main-nav .is-active::after {
    content: ""; position: absolute; left: -6px; right: -6px; top: 27px;
    height: 1px; background: var(--white);
  }

  .hero {
    position: absolute; left: 0; top: 61px; width: 1200px; height: 539px;
    background: linear-gradient(100deg, var(--hero-dark) 0%, #2a2426 28%, var(--hero-mid) 48%, #8c8a92 70%, var(--hero-light) 100%);
  }
  .partner-badge {
    position: absolute; left: 99px; top: 86px; width: 171px; height: 60px;
    border-radius: 8px; background: var(--badge-silver);
    box-shadow: 0 2px 6px rgba(0,0,0,0.4); overflow: hidden;
  }
  .partner-badge::before {
    content: ""; position: absolute; left: 0; top: 0; width: 60px; height: 60px;
    background: var(--badge-blue);
  }
  .hero-title {
    position: absolute; left: 95px; top: 229px; line-height: 50px;
    font-family: "Mulish", sans-serif; font-weight: 700; font-size: 41px;
    white-space: nowrap; letter-spacing: 0.2px;
  }
  .hero-title sup { font-size: 17px; position: relative; top: -10px; margin-left: 2px; }
  .hero-lede {
    position: absolute; left: 117px; top: 311px; width: 640px;
    text-align: center; font-size: 18.5px; line-height: 23px;
  }
  .hero-lede span { display: block; white-space: nowrap; }
  .store-button {
    position: absolute; top: 421px; height: 55px;
    background: var(--brand-orange); display: flex; align-items: stretch;
    box-shadow: 2px 3px 5px rgba(0,0,0,0.45);
    font-family: "Lato", sans-serif; color: var(--white);
  }
  .store-button .icon-cell {
    width: 60px; border-right: 1px solid var(--white);
    display: flex; align-items: center; justify-content: center;
  }
  .store-button .icon-cell span { width: 24px; height: 24px; background: var(--white); border-radius: 50%; }
  .store-button .label {
    flex: 1; display: flex; flex-direction: column; justify-content: center;
    align-items: center; line-height: 1.1;
  }
  .store-button .label small { font-size: 13px; font-weight: 700; }
  .store-button .label strong { font-size: 18px; font-weight: 400; margin-top: 3px; }
  .store-vault { left: 221px; width: 193px; }
  .store-depot { left: 434px; width: 213px; }

  .site-footer {
    position: absolute; left: 0; top: 600px; width: 1200px; height: 43px;
    background: var(--footer-bg);
  }
  .copyright {
    position: absolute; left: 99px; top: 14px;
    font-family: "Lato", sans-serif; font-size: 12.5px;
  }
  .social-links { position: absolute; left: 970px; top: 8px; display: flex; gap: 9px; }
  .social-links a { width: 26px; height: 26px; border-radius: 50%; display: block; }
  .social-a { background: var(--social-blue); }
  .social-b { background: var(--social-sky); }
  .social-c { background: var(--social-red); }
  .social-d { background: var(--social-navy); }
</style>
</head>
<body>
  <header class="site-header">
    <a class="brand" href="#">
      <span class="brand-mark"></span>
      <span class="brand-name">velmora</span>
    </a>
    <nav class="main-nav">
      <a class="is-active" href="#" style="left:518px">Home</a>
      <a href="#" style="left:622px">Product</a>
      <a href="#" style="left:722px;top:16px">Blog</a>
      <a href="#" style="left:812px">About</a>
      <a href="#" style="left:924px">Our Team</a>
      <a href="#" style="left:1046px">Contact</a>
    </nav>
  </header>

  <main class="hero" role="img" aria-label="Photo of a woman watching a music video on a smartphone held in her hand">
    <div class="partner-badge" aria-label="Certified developer partner badge"></div>
    <h1 class="hero-title">High Quality Mobile Engagement<sup>TM</sup></h1>
    <p class="hero-lede"><span>We engage mobile audiences with the right video content at the</span><span>perfect moment.</span></p>
    <a class="store-button store-vault" href="#">
      <span class="icon-cell"><span></span></span>
      <span class="label"><small>Available on</small><strong>APP VAULT</strong></span>
    </a>
    <a class="store-button store-depot" href="#">
      <span class="icon-cell"><span></span></span>
      <span class="label"><small>Available on</small><strong>PLAY DEPOT</strong></span>
    </a>
  </main>

  <footer class="site-footer">
    <p class="copyright">Copyright © 2016 Velmora Media. All Rights Reserved.</p>
    <nav class="social-links" aria-label="Social links">
      <a class="social-a" href="#" aria-label="Social profile one"></a>
      <a class="social-b" href="#" aria-label="Social profile two"></a>
      <a class="social-c" href="#" aria-label="Social profile three"></a>
      <a class="social-d" href="#" aria-label="Social profile four"></a>
    </nav>
  </footer>
</body>
</html>
```